Business Card Design for Marketing Firm

Looking for business card design for higher end marketing firm. Clean but impressionable/trendy. We are a marketing firm that represents manufacturers in the foodservice equipment and supply industry. Our customers are end users such has hotels, restaurants, country clubs, convention centers and casinos as well as distributors of restaurants supplies and equipment, and manufacturers of foodservice equipment and supplies.
Target Market(s)
Hotels, Restaurants, Supply & Equipment Distributors, Foodservice Manufacturers
Industry/Entity Type
Foodservice/Hospitality
Contact Information for Business Card
Name, Title, Contact Number, Email, Website, Social Media, Address
Requirements
Must have
- Clean & Simple but Serious and Impressionable

```html
<!DOCTYPE html>
<html lang="en">
<head>
<meta charset="utf-8">
<title>Meridian Hospitality Reps – Business Card</title>
<link rel="stylesheet" href="https://fonts.googleapis.com/css2?family=Open+Sans:wght@400;600;700&display=swap">
<style>
  :root {
    --navy: #29296f;
    --white: #ffffff;
    --ink: #222233;
    --backdrop: #e2e2df;
  }
  * { margin: 0; padding: 0; box-sizing: border-box; }
  html, body { width: 1200px; height: 801px; overflow: hidden; }
  body {
    background: var(--backdrop);
    font-family: "Open Sans", Arial, sans-serif;
    position: relative;
  }
  .card {
    position: absolute;
    top: 245px;
    width: 540px;
    height: 310px;
    border-radius: 18px;
    background: var(--white);
    overflow: hidden;
    box-shadow: 0 10px 28px rgba(0,0,0,0.18);
  }
  .card-front { left: 45px; }
  .card-back { left: 615px; }

  /* navy contact panel */
  .contact-panel {
    position: absolute;
    left: 290px;
    right: 0;
    top: 100px;
    bottom: 0;
    background: var(--navy);
    border-top-left-radius: 120px;
  }

  /* company name */
  .company-name {
    position: absolute;
    color: var(--navy);
    font-weight: 600;
    text-transform: uppercase;
    letter-spacing: 0.05em;
    line-height: 1.3;
  }
  .card-front .company-name { left: 32px; top: 130px; width: 220px; font-size: 17px; }
  .card-back .company-name {
    left: 0; right: 0; top: 126px;
    text-align: center; font-size: 24px; white-space: nowrap;
  }

  /* person */
  .person { position: absolute; right: 30px; top: 18px; text-align: right; }
  .person-name { color: var(--navy); font-weight: 700; font-size: 17px; letter-spacing: 0.02em; line-height: 1.2; }
  .person-title { color: var(--ink); font-size: 11px; }
  .accent-bar { position: absolute; right: 12px; top: 0; width: 9px; height: 30px; background: var(--navy); }

  /* contact */
  .contact { position: absolute; right: 16px; top: 132px; list-style: none; color: var(--white); font-size: 11px; line-height: 16px; text-align: right; }
  .contact li { display: flex; justify-content: flex-end; align-items: center; gap: 6px; }
  .contact .gap { margin-top: 8px; }
  .contact svg { width: 10px; height: 10px; flex: none; }
  .contact .no-icon::after { content: ""; width: 10px; }

  /* social */
  .social { position: absolute; left: 50%; top: 180px; transform: translateX(-50%); display: flex; gap: 6px; list-style: none; }
  .social li { width: 16px; height: 16px; border-radius: 50%; background: var(--navy); }
</style>
</head>
<body>

<section class="card card-front" aria-label="Business card front">
  <div class="contact-panel"></div>
  <div class="accent-bar"></div>
  <div class="person">
    <p class="person-name">DANIEL HARTLEY</p>
    <p class="person-title">Managing Director</p>
  </div>
  <p class="company-name">Meridian Hospitality Reps</p>
  <ul class="contact">
    <li class="no-icon">Your address, City</li>
    <li class="no-icon">State, Zip 1234</li>
    <li class="gap">123 456 789
      <svg viewBox="0 0 10 10"><path d="M2 1 L4 1 L4.6 3 L3.4 3.8 Q4.4 5.8 6.2 6.6 L7 5.4 L9 6 L9 8 Q5 9 2.4 6.4 Q0.6 4 2 1 Z" fill="var(--white)"/></svg>
    </li>
    <li>123 456 789
      <svg viewBox="0 0 10 10"><path d="M2 1 L4 1 L4.6 3 L3.4 3.8 Q4.4 5.8 6.2 6.6 L7 5.4 L9 6 L9 8 Q5 9 2.4 6.4 Q0.6 4 2 1 Z" fill="var(--white)"/></svg>
    </li>
    <li>info@meridianreps.com
      <svg viewBox="0 0 10 10"><rect x="0.5" y="2" width="9" height="6.5" fill="none" stroke="var(--white)" stroke-width="1"/><path d="M0.5 2 L5 5.6 L9.5 2" fill="none" stroke="var(--white)" stroke-width="1"/></svg>
    </li>
    <li>www.meridianreps.com
      <svg viewBox="0 0 10 10"><circle cx="5" cy="5" r="4.3" fill="none" stroke="var(--white)" stroke-width="1"/><ellipse cx="5" cy="5" rx="1.8" ry="4.3" fill="none" stroke="var(--white)" stroke-width="0.8"/><path d="M0.7 5 H9.3" stroke="var(--white)" stroke-width="0.8"/></svg>
    </li>
  </ul>
</section>

<section class="card card-back" aria-label="Business card back">
  <p class="company-name">Meridian Hospitality Reps</p>
  <ul class="social" aria-label="Social media links">
    <li></li><li></li><li></li><li></li><li></li><li></li>
  </ul>
</section>

</body>
</html>
```